Amber Meadow Business Card and Logo

Nutrition and Wellness Store Front. I sell supplements, herbs, tinctures, Loose Leaf Teas, natural snacks and drinks including gluten free. classes: Fitness; health and wellness; community health and wellness hub. It is a "shabby chic" store front. It is white and my accent color is turqouise I will be adding some jewelry, stones and rocks and jewelery. I am a Certified Herbalist and Certified Nutrition and Wellness Consultant, a Reiki Practitioner and Kavolo instructor.

Target Market(s)

health and wellness seekers, fitness, baby boomer

Industry/Entity Type

Business

Contact Information for Business Card

Amber Meadow Nutrition and Wellness
Delia Marchetti Certified Herbalist , Certified Nutrition and Wellness Consultant, Reiki Practitioner, Kavolo Instructor

Font styles to use
Serif

Colors
33a6d7
3176b5
33b8a4

Requirements
Must have
• A picture that represents two mountain peaks with a floral accent.

```html
<!DOCTYPE html>
<html lang="en">
<head>
<meta charset="utf-8">
<title>Amber Meadow Nutrition and Wellness – Business Card</title>
<link rel="stylesheet" href="https://fonts.googleapis.com/css2?family=Open+Sans:wght@300;400;700&display=swap">
<style>
  :root {
    --page-bg: #ecebe8;
    --photo-top: #d98fb8;
    --photo-bottom: #5e7f45;
    --band-turquoise: rgba(51, 184, 164, 0.7);
    --band-edge: rgba(51, 166, 215, 0.6);
    --card-edge: #3176b5;
    --text-white: #ffffff;
    --text-soft: rgba(255, 255, 255, 0.92);
    --title-lime: #d8f06a;
  }
  * { margin: 0; padding: 0; box-sizing: border-box; }
  html, body {
    width: 1200px;
    height: 1022px;
    overflow: hidden;
    background: var(--page-bg);
    font-family: "Open Sans", Arial, sans-serif;
  }
  .card {
    position: absolute;
    left: 75px;
    top: 211px;
    width: 1050px;
    height: 600px;
    border-radius: 26px;
    overflow: hidden;
    border: 6px solid var(--card-edge);
    box-shadow: 0 18px 40px rgba(0, 0, 0, 0.25);
  }
  .card__photo {
    position: absolute;
    inset: 0;
    background: linear-gradient(180deg, var(--photo-top) 0%, var(--photo-bottom) 100%);
  }
  .card__band {
    position: absolute;
    left: 0;
    right: 0;
    top: 330px;
    height: 190px;
    background: var(--band-turquoise);
    border-top: 2px solid var(--band-edge);
    border-bottom: 2px solid var(--band-edge);
  }
  .brand {
    position: absolute;
    left: 54px;
    top: 196px;
    display: flex;
    align-items: center;
    gap: 16px;
    color: var(--text-soft);
  }
  .brand__mark {
    width: 60px;
    height: 60px;
    border-radius: 50%;
    border: 3px solid var(--text-soft);
    flex: none;
  }
  .brand__name {
    font-weight: 300;
    font-size: 30px;
    line-height: 1.2;
  }
  .person {
    position: absolute;
    right: 60px;
    top: 150px;
    text-align: right;
    color: var(--text-white);
  }
  .person__name {
    font-weight: 700;
    font-size: 54px;
    line-height: 1.1;
  }
  .person__title {
    font-weight: 400;
    font-size: 30px;
    margin-top: 4px;
    color: var(--title-lime);
  }
  .credentials {
    position: absolute;
    left: 54px;
    top: 356px;
    list-style: none;
    color: var(--text-white);
    font-weight: 400;
    font-size: 31px;
    line-height: 1.35;
  }
  .credentials li {
    display: flex;
    align-items: center;
    gap: 12px;
  }
  .credentials svg { width: 24px; height: 24px; flex: none; }
</style>
</head>
<body>
  <section class="card">
    <div class="card__photo" role="img" aria-label="Photograph of two snowy mountain peaks under a pink sky above a meadow of purple wildflowers"></div>
    <div class="card__band"></div>

    <div class="brand">
      <span class="brand__mark"></span>
      <p class="brand__name">Amber Meadow Nutrition<br>and Wellness</p>
    </div>

    <div class="person">
      <h1 class="person__name">Delia Marchetti</h1>
      <p class="person__title">Certified Herbalist</p>
    </div>

    <ul class="credentials">
      <li><svg viewBox="0 0 24 24"><path d="M3 13l6 6L21 5" fill="none" stroke="#fff" stroke-width="3.5" stroke-linecap="round" stroke-linejoin="round"/></svg>Reiki Practitioner</li>
      <li><svg viewBox="0 0 24 24"><path d="M3 13l6 6L21 5" fill="none" stroke="#fff" stroke-width="3.5" stroke-linecap="round" stroke-linejoin="round"/></svg>Kavolo Instructor</li>
      <li><svg viewBox="0 0 24 24"><path d="M3 13l6 6L21 5" fill="none" stroke="#fff" stroke-width="3.5" stroke-linecap="round" stroke-linejoin="round"/></svg>Certified Nutrition and Wellness Consultant</li>
    </ul>
  </section>
</body>
</html>
```